wealth management firm, professional group, new model

we have a logo that works but we need a card, white background using our colors...clean look

our tag line if can be used in

The Path from Planning to Wealth

```html
<!DOCTYPE html>
<html lang="en">
<head>
<meta charset="utf-8">
<title>Arcwell Wealth Partners – Business Card</title>
<link href="https://fonts.googleapis.com/css2?family=Montserrat:wght@400;500&display=swap" rel="stylesheet">
<style>
  :root {
    --backdrop: #262626;
    --navy: #14284a;
    --navy-deep: #112241;
    --paper: #f1f1f1;
    --paper-shade: #e4e4e4;
    --steel: #9aa6ba;
    --on-navy: #e6e9ef;
  }
  * { margin: 0; padding: 0; box-sizing: border-box; }
  html, body {
    width: 1200px; height: 576px; overflow: hidden;
    background: var(--backdrop);
    font-family: "Montserrat", sans-serif;
  }
  .canvas { position: relative; width: 1200px; height: 576px; }
  .card {
    position: absolute; top: 138px; height: 294px;
    border-radius: 9px; overflow: hidden;
  }
  /* Back side */
  .card-back {
    left: 102px; width: 485px;
    background: linear-gradient(180deg, var(--navy) 0%, var(--navy-deep) 100%);
  }
  .back-wordmark {
    position: absolute; top: 128px; left: 0; right: 0;
    text-align: center; color: var(--steel);
    font-size: 30px; font-weight: 400; letter-spacing: 12px;
    padding-left: 12px;
  }
  .back-tagline {
    position: absolute; top: 249px; left: 0; right: 0;
    text-align: center; color: var(--on-navy);
    font-size: 13px; letter-spacing: 0.6px;
  }
  /* Front side */
  .card-front {
    left: 596px; width: 481px;
    background: linear-gradient(135deg, var(--paper) 0%, var(--paper-shade) 100%);
  }
  .brand {
    position: absolute; left: 27px; top: 118px; width: 200px;
    text-align: center; color: var(--navy); font-weight: 400;
  }
  .brand-name { font-size: 27px; letter-spacing: 5px; padding-left: 5px; line-height: 1; }
  .brand-sub { font-size: 13px; letter-spacing: 2px; padding-left: 2px; margin-top: 20px; }
  .person { position: absolute; left: 268px; top: 72px; color: var(--navy); }
  .person-name { font-size: 22px; font-weight: 500; line-height: 1.1; }
  .person-title { font-size: 13px; margin-top: 3px; }
  .contact-list { list-style: none; margin-top: 10px; }
  .contact-list li {
    display: flex; align-items: center; gap: 8px;
    font-size: 12.5px; height: 20px;
  }
  .contact-list svg { width: 11px; height: 11px; fill: var(--navy); flex: none; }
  .footer-band { position: absolute; left: 0; bottom: 0; width: 481px; height: 38px; }
  .front-tagline {
    position: absolute; right: 19px; bottom: 11px;
    color: var(--on-navy); font-size: 13px; letter-spacing: 0.6px;
  }
</style>
</head>
<body>
<main class="canvas">
  <section class="card card-back" aria-label="Card back">
    <div class="back-wordmark">ARCWELL</div>
    <p class="back-tagline">The Path from Planning to Wealth</p>
  </section>

  <section class="card card-front" aria-label="Card front">
    <div class="brand">
      <div class="brand-name">ARCWELL</div>
      <div class="brand-sub">WEALTH PARTNERS</div>
    </div>

    <div class="person">
      <div class="person-name">Daniel Reyes</div>
      <div class="person-title">Managing Director</div>
      <ul class="contact-list">
        <li>
          <svg viewBox="0 0 12 12" aria-hidden="true"><path d="M1 4c0-2 2-3 5-3s5 1 5 3v1H8.5V4h-5v1H1zM3 6h6l2 3v2H1V9z"/></svg>
          555-214-8830
        </li>
        <li>
          <svg viewBox="0 0 12 12" aria-hidden="true"><path d="M0 2h12v8H0zM1 3v.4l5 3.3 5-3.3V3z" fill-rule="evenodd"/></svg>
          daniel@arcwellpartners.com
        </li>
        <li>
          <svg viewBox="0 0 12 12" aria-hidden="true"><circle cx="6" cy="6" r="5.5"/><path d="M.5 6h11M6 .5v11M2 3h8M2 9h8" stroke="#f1f1f1" stroke-width=".8" fill="none"/></svg>
          www.arcwellpartners.com
        </li>
      </ul>
    </div>

    <svg class="footer-band" viewBox="0 0 481 38" aria-hidden="true">
      <path d="M0 26 H176 L172 38 H0 Z" fill="var(--navy)"/>
      <path d="M214 0 H481 V38 H182 L200 6 Q203 0 214 0 Z" fill="var(--navy)"/>
    </svg>
    <p class="front-tagline">The Path from Planning to Wealth</p>
  </section>
</main>
</body>
</html>
```